Website Design for a holiday home letting busines

We require a redesign of our present website www.pinebrookstays.com. We want the website to stand out and look professional and clean to make holiday hunters want to book a caravan or lodge holiday with us. Our logo is red however we DO NOT want the website to be red. We want a natural colour scheme.

The final design should communicate that we are a professional company to book with.

On the home page we require;
Overview of company
Photo
Search box for holiday (check in)
Late Deals
Reviews
News

We would like the following pages designed; home page, available dates page, caravans page, content page.

The website should be responsive for smart phones. One website I do like is http://www.verdoliso.be/nl/

Target Market(s)

Families

Industry/Entity Type

Travel

Number of Pages Required

5+ page

Font styles to use
Serif

Requirements
Must have
• The project must be responsive for mobile phones and tablets.
• Ability to search for holiday home holidays
• We want a natural colour scheme.
Nice to have
• A style we like is http://www.verdoliso.be/nl/
Should not have
• Do not use red as a colour for the website. Our logo is red so this is the only time we want this used.

```html
<!DOCTYPE html>
<html lang="en">
<head>
<meta charset="utf-8">
<title>Pinebrook Stays – Holiday Caravans and Lodges</title>
<link href="https://fonts.googleapis.com/css2?family=Lora:ital,wght@0,400;0,600;0,700;1,400&family=Open+Sans:wght@400;600;700&display=swap" rel="stylesheet">
<style>
:root{
  --ink:#2f2f2f;
  --muted:#7a7a7a;
  --line:#e2e2e2;
  --paper:#ffffff;
  --header:#2a2a2a;
  --nav:#353535;
  --brand:#c9252c;
  --accent:#4f6b35;
  --accent-dark:#3b5228;
  --wood:#8a6d4b;
  --dark-box:#3b3b3b;
  --footer:#2d2d2d;
  --footer-bar:#3b4a2c;
  --shade:rgba(18,18,18,.64);
  --serif:"Lora",Georgia,serif;
}
*{box-sizing:border-box;margin:0;padding:0}
html,body{width:1200px;height:2792px;overflow:hidden}
body{font-family:"Open Sans",Arial,sans-serif;color:var(--ink);background:var(--paper);position:relative}
.page{position:absolute;inset:0}
.abs{position:absolute}

/* header */
.site-header{position:absolute;left:0;top:0;width:1200px;height:112px;background:var(--header)}
.brand{position:absolute;left:80px;top:34px;display:flex;align-items:center;gap:12px}
.brand-mark{width:42px;height:42px;border-radius:50%;background:var(--brand)}
.brand-name{font-family:var(--serif);font-size:26px;font-weight:700;color:var(--brand)}
.contact{position:absolute;right:80px;top:42px;display:flex;gap:32px;font-size:15px;color:#ddd}
.contact span{display:flex;align-items:center;gap:8px}
.main-nav{position:absolute;left:0;top:112px;width:1200px;height:40px;background:var(--nav);display:flex;justify-content:center;gap:38px;align-items:center;font-size:14px;color:#e8e8e8}

/* hero */
.hero{position:absolute;left:0;top:152px;width:1200px;height:568px;background:linear-gradient(180deg,#3a3f7a 0%,#6a4c8c 38%,#c46a6a 62%,#2d5f7a 72%,#1d3d55 100%)}
.hero-panel{position:absolute;right:80px;top:90px;width:300px;color:#fff}
.hero-panel h1{font-family:var(--serif);font-size:34px;font-weight:700;line-height:1.15}
.hero-panel p{font-size:14px;margin-top:10px;line-height:1.5;color:#eee}
.hero-panel h2{font-family:var(--serif);font-size:20px;font-weight:700;margin-top:36px;letter-spacing:1px}
.field{height:38px;background:#fff;margin-top:12px;border-radius:2px}
.field-row{display:flex;gap:10px}
.field-row .field{flex:1}
.search-btn{margin-top:14px;height:42px;background:var(--accent);color:#fff;font-weight:700;display:flex;align-items:center;justify-content:center;font-size:15px}
.hero-dots{position:absolute;left:0;right:0;bottom:24px;display:flex;justify-content:center;gap:10px}
.dot{width:10px;height:10px;border-radius:50%;background:#bbb}
.dot.on{background:#fff}

/* sections */
.section-title{position:absolute;left:0;width:1200px;text-align:center;font-family:var(--serif);font-size:30px;font-weight:600}
.see-all{position:absolute;left:0;width:1200px;text-align:center;font-size:14px;color:var(--accent);font-weight:600}
.photo{background:linear-gradient(135deg,#b89a78,#e6d6c0 55%,#8b6e52)}
.photo.cool{background:linear-gradient(135deg,#9aa7b0,#e4e1da 55%,#7e6c5c)}
.card-name{font-family:var(--serif);font-size:18px;font-weight:700;text-align:center}
.meta-row{display:flex;justify-content:center;gap:14px;font-size:12px;color:var(--muted)}
.meta{display:flex;align-items:center;gap:6px;border:1px solid var(--line);padding:5px 10px}
.meta b{color:var(--ink)}
.arrows{position:absolute;display:flex;gap:8px}
.arrow-btn{width:28px;height:28px;border-radius:50%;background:#ddd}
.pager{position:absolute;left:0;width:1200px;display:flex;justify-content:center;gap:10px}
.pager .dot{background:#cfcfcf}
.pager .dot.on{background:#555}

.deal-name{font-family:var(--serif);font-size:14px;font-weight:700}
.deal-name em{font-style:normal;color:var(--accent);font-weight:600}
.price{background:var(--dark-box);color:#fff;font-weight:700;font-size:15px;display:flex;align-items:center;justify-content:center}

/* reviews */
.reviews{position:absolute;left:0;top:1720px;width:1200px;height:420px;background:linear-gradient(180deg,#b9a68c,#8d7a64)}
.review{position:absolute;top:72px;width:330px;height:290px;background:var(--paper);text-align:center;padding:70px 26px 0}
.avatar{position:absolute;left:50%;top:-44px;width:88px;height:88px;margin-left:-44px;border-radius:50%;background:linear-gradient(135deg,#c9b39a,#7d6a56);border:5px solid #fff}
.review h3{font-family:var(--serif);font-size:19px;font-weight:700;color:var(--accent-dark)}
.review small{display:block;font-size:13px;color:var(--muted);margin-top:2px}
.review p{font-family:var(--serif);font-size:14px;line-height:1.6;color:var(--muted);margin-top:16px;font-style:italic}

/* blog */
.blog-title{position:absolute;left:80px;top:2176px;font-family:var(--serif);font-size:30px;font-weight:600}
.post{position:absolute;width:320px}
.post h4{font-family:var(--serif);font-size:16px;font-weight:700;color:var(--accent-dark)}
.post p{font-size:13px;color:var(--muted);margin-top:4px;line-height:1.5}
.social-box{position:absolute;left:760px;top:2180px;width:360px;height:350px;border:1px solid var(--line);padding:18px}
.social-head{display:flex;align-items:center;gap:10px}
.social-head .sq{width:44px;height:44px;background:var(--brand)}
.social-head span{font-family:var(--serif);font-size:16px;font-weight:700;color:var(--brand)}
.social-sub{font-size:12px;color:var(--muted);margin-top:14px}
.fans{display:grid;grid-template-columns:repeat(4,64px);gap:12px;margin-top:14px}
.fan{width:64px;height:64px;background:linear-gradient(135deg,#cdb9a3,#8a7764)}
.fans .fan:nth-child(even){background:linear-gradient(135deg,#a9a39a,#5f5a54)}

/* footer */
.site-footer{position:absolute;left:0;top:2560px;width:1200px;height:232px;background:var(--footer);color:#ccc}
.footer-bar{position:absolute;left:0;top:200px;width:1200px;height:32px;background:var(--footer-bar);font-size:12px;color:#eee;display:flex;align-items:center;justify-content:center}
.news h5{font-family:var(--serif);font-size:14px;font-weight:700;color:#fff;letter-spacing:1px}
.news-form{display:flex;margin-top:14px}
.news-form .in{width:230px;height:38px;background:#fff}
.news-form .go{width:40px;height:38px;background:var(--accent)}
.socials{display:flex;gap:12px;margin-top:22px}
.socials i{width:38px;height:38px;border-radius:50%;background:#555;display:block}
.links{position:absolute;top:34px;font-size:13px;line-height:24px}

/* modal */
.shade{position:absolute;inset:0;background:var(--shade);z-index:5}
.promo{position:absolute;left:264px;top:228px;width:672px;height:452px;z-index:6;border:4px solid #fff;overflow:hidden}
.promo-photo{position:absolute;inset:0;background:linear-gradient(180deg,#8fb7d6 0%,#f0c27a 38%,#e8743a 58%,#6b3b2a 78%,#2a2020 100%)}
.promo-text{position:absolute;left:0;right:0;top:30px;text-align:center}
.promo-text h2{font-family:var(--serif);font-size:54px;font-weight:700;color:var(--accent-dark);line-height:1}
.promo-text p{font-size:16px;font-weight:600;color:#2a2a2a;margin-top:10px}
.book-btn{display:inline-flex;align-items:center;gap:10px;margin-top:18px;background:#fff;border:2px solid var(--accent);color:var(--accent-dark);font-weight:700;font-size:17px;padding:8px 18px;border-radius:4px}
.promo-dots{position:absolute;left:0;right:0;bottom:12px;display:flex;justify-content:center;gap:8px}
.promo-dots .dot{width:8px;height:8px}
</style>
</head>
<body>
<div class="page">

<header class="site-header">
  <div class="brand"><div class="brand-mark"></div><div class="brand-name">Pinebrook Stays</div></div>
  <div class="contact">
    <span><svg width="16" height="16" viewBox="0 0 24 24"><path fill="#ddd" d="M6.6 10.8a15 15 0 006.6 6.6l2.2-2.2c.3-.3.7-.4 1-.2 1.1.4 2.3.6 3.6.6.6 0 1 .4 1 1V20c0 .6-.4 1-1 1A17 17 0 013 4c0-.6.4-1 1-1h3.5c.6 0 1 .4 1 1 0 1.3.2 2.5.6 3.6.1.3 0 .7-.2 1z"/></svg>01632 960 000</span>
    <span><svg width="18" height="14" viewBox="0 0 24 18"><rect x="1" y="1" width="22" height="16" fill="none" stroke="#ddd" stroke-width="2"/><path d="M1 1l11 9 11-9" fill="none" stroke="#ddd" stroke-width="2"/></svg>hello@pinebrookstays.com</span>
  </div>
</header>
<nav class="main-nav">
  <span>Home</span><span>News</span><span>Reviews</span><span>Caravans &amp; Lodges</span><span>2016 / 2017 Holidays</span><span>Popular Parks</span><span>Fernhollow Park</span><span>Contact Us</span>
</nav>

<section class="hero" role="img" aria-label="Photo of water villas on a lagoon at sunset">
  <div class="hero-panel">
    <h1>Holiday Rentals</h1>
    <p>Relaxing caravan and lodge breaks at Fernhollow Park for the whole family.</p>
    <h2>PLAN YOUR VACATION</h2>
    <div class="field"></div>
    <div class="field-row"><div class="field"></div><div class="field"></div></div>
    <div class="search-btn">Search</div>
  </div>
  <div class="hero-dots"><span class="dot on"></span><span class="dot"></span><span class="dot"></span></div>
</section>

<h2 class="section-title" style="top:776px">Our caravans and lodges</h2>
<div class="see-all" style="top:828px">See all Items →</div>
<div class="arrows" style="left:1056px;top:780px"><span class="arrow-btn"></span><span class="arrow-btn"></span></div>

<div class="abs" style="left:80px;top:880px;width:330px">
  <div class="photo" style="height:208px" role="img" aria-label="Photo of a caravan living room"></div>
  <div class="card-name" style="margin-top:28px">The Harwood</div>
  <div class="meta-row" style="margin-top:24px"><span class="meta">Bedrooms <b>2</b></span><span class="meta">Sleeps <b>6</b></span></div>
</div>
<div class="abs" style="left:435px;top:880px;width:330px">
  <div class="photo cool" style="height:208px" role="img" aria-label="Photo of a lodge lounge and kitchen"></div>
  <div class="card-name" style="margin-top:28px">The Ashby</div>
  <div class="meta-row" style="margin-top:24px"><span class="meta">Bedrooms <b>3</b></span><span class="meta">Sleeps <b>8</b></span></div>
</div>
<div class="abs" style="left:790px;top:880px;width:330px">
  <div class="photo" style="height:208px" role="img" aria-label="Photo of a caravan lounge with sofas"></div>
  <div class="card-name" style="margin-top:28px">The Calder</div>
  <div class="meta-row" style="margin-top:24px"><span class="meta">Bedrooms <b>2</b></span><span class="meta">Sleeps <b>4</b></span></div>
</div>
<div class="pager" style="top:1258px"><span class="dot on"></span><span class="dot"></span></div>

<h2 class="section-title" style="top:1296px">Late Deals</h2>
<div class="abs" style="left:80px;top:1372px;width:245px">
  <div class="photo" style="height:160px" role="img" aria-label="Photo of a caravan interior"></div>
  <div class="deal-name" style="margin-top:20px">The Marlow <em>£149 · 3 nights</em></div>
  <div style="display:flex;gap:8px;margin-top:16px"><div class="meta-row" style="flex-direction:column;gap:4px"><span class="meta">Bedrooms <b>2</b></span><span class="meta">Sleeps <b>6</b></span></div><div class="price" style="flex:1">£149.00</div></div>
</div>
<div class="abs" style="left:345px;top:1372px;width:245px">
  <div class="photo cool" style="height:160px" role="img" aria-label="Photo of a lodge interior"></div>
  <div class="deal-name" style="margin-top:20px">The Calder <em>£149 · 3 nights</em></div>
  <div style="display:flex;gap:8px;margin-top:16px"><div class="meta-row" style="flex-direction:column;gap:4px"><span class="meta">Bedrooms <b>3</b></span><span class="meta">Sleeps <b>8</b></span></div><div class="price" style="flex:1">£149.00</div></div>
</div>
<div class="abs" style="left:610px;top:1372px;width:245px">
  <div class="photo" style="height:160px" role="img" aria-label="Photo of a caravan lounge"></div>
  <div class="deal-name" style="margin-top:20px">The Marlow <em>£149 · 4 nights</em></div>
  <div style="display:flex;gap:8px;margin-top:16px"><div class="meta-row" style="flex-direction:column;gap:4px"><span class="meta">Bedrooms <b>2</b></span><span class="meta">Sleeps <b>4</b></span></div><div class="price" style="flex:1">£149.00</div></div>
</div>
<div class="abs" style="left:875px;top:1372px;width:245px">
  <div class="photo cool" style="height:160px" role="img" aria-label="Photo of a lodge dining area"></div>
  <div class="deal-name" style="margin-top:20px">The Calder <em>£149 · 4 nights</em></div>
  <div style="display:flex;gap:8px;margin-top:16px"><div class="meta-row" style="flex-direction:column;gap:4px"><span class="meta">Bedrooms <b>3</b></span><span class="meta">Sleeps <b>6</b></span></div><div class="price" style="flex:1">£149.00</div></div>
</div>

<section class="reviews" role="img" aria-label="Soft background photo of the holiday park">
  <div class="review" style="left:88px"><div class="avatar" role="img" aria-label="Guest portrait"></div><h3>Hannah Cole</h3><small>Stayed in The Ashby</small><p>"We had a wonderful week, the lodge was spotless and the staff were so friendly. We will book again next summer."</p></div>
  <div class="review" style="left:435px"><div class="avatar" role="img" aria-label="Guest portrait"></div><h3>Megan Hart</h3><small>Stayed in The Harwood</small><p>"Lovely caravan with everything we needed, the children loved the park."</p></div>
  <div class="review" style="left:782px"><div class="avatar" role="img" aria-label="Guest portrait"></div><h3>Laura Finch</h3><small>Stayed in The Calder</small><p>"Easy to book, great value and a very clean caravan. A perfect family break we would recommend."</p></div>
  <div class="pager" style="top:390px"><span class="dot on"></span><span class="dot"></span><span class="dot"></span></div>
</section>

<h2 class="blog-title">Blog &amp; News</h2>
<div class="post" style="left:80px;top:2244px"><h4>Fireworks Weekend</h4><p>Join us for a night of colour and fun at the park this autumn.</p></div>
<div class="post" style="left:420px;top:2244px"><h4>Easter Family Fun Day</h4><p>Egg hunts, games and treats for all the family this Easter.</p></div>
<div class="post" style="left:80px;top:2348px"><h4>Live Music Night At Fernhollow Park</h4><p>An evening of live bands in the clubhouse for every guest.</p></div>
<div class="post" style="left:420px;top:2348px"><h4>Very Clean on arrival</h4><p>Our guests tell us why our caravans feel like home.</p></div>
<aside class="social-box">
  <div class="social-head"><div class="sq"></div><span>Pinebrook Stays</span></div>
  <div class="social-sub">1,240 people follow Pinebrook Stays</div>
  <div class="fans" role="img" aria-label="Follower profile photos">
    <div class="fan"></div><div class="fan"></div><div class="fan"></div><div class="fan"></div>
    <div class="fan"></div><div class="fan"></div><div class="fan"></div><div class="fan"></div>
  </div>
</aside>

<footer class="site-footer">
  <div class="news abs" style="left:80px;top:34px">
    <h5>JOIN OUR NEWSLETTER</h5>
    <div class="news-form"><div class="in"></div><div class="go"></div></div>
    <div class="socials"><i></i><i></i><i></i><i></i></div>
  </div>
  <div class="links" style="left:472px">About us<br>News<br>Caravans &amp; Lodges<br>2016 Holidays<br>Late Deals</div>
  <div class="links" style="left:700px">Fernhollow Park<br>Park Attractions<br>Guest Guide<br>Contact Us<br>Reviews</div>
  <div class="links" style="left:920px">Frequently Asked Questions<br>Park Information Guide<br>Privacy Policy<br>Booking Terms</div>
  <div class="footer-bar">Pinebrook Stays © 2016 All Rights Reserved · Terms of use and Privacy Policy</div>
</footer>

<div class="shade"></div>
<div class="promo">
  <div class="promo-photo" role="img" aria-label="Photo of parasols and sun loungers by a pool at sunset"></div>
  <div class="promo-text">
    <h2>Beat The Rush</h2>
    <p>Book Your 2016 Holidays Fernhollow Park Today!</p>
    <span class="book-btn">Book Now! <svg width="18" height="18" viewBox="0 0 20 20"><circle cx="10" cy="10" r="9" fill="var(--accent)"/><path d="M8 5l5 5-5 5" fill="none" stroke="#fff" stroke-width="2.4"/></svg></span>
  </div>
  <div class="promo-dots"><span class="dot on"></span><span class="dot"></span><span class="dot"></span></div>
</div>

</div>
</body>
</html>
```